first fantastic look and impression

We are looking for a concept for letterhead, business card, emailfooter and template for invoices or offers for our company in the consultation business.
The dancer is a symbol who we are: it looks simple, but there is a lot of hard work and many years of training in this movement. The look is also what we want: elegant, modern, strong, with a touch of extravaganza
Target Market(s)
Hotelbusiness , Consulting
Font styles to use
Sans Serif
Other font styles liked:
- please give us a option we are open
Requirements
Must have
- We are not typical consultants but sparring partners and coaches for the hotel and that should also be expressed in the design. Maybe there is an icon that supports the whole thing. We are more modern and bolder than our industry colleagues.
we are modern, fresh, agile, fast
Nice to have
- a icon

```html
<!DOCTYPE html>
<html lang="en">
<head>
<meta charset="utf-8">
<title>Brennwald+Partner – Stationery</title>
<link href="https://fonts.googleapis.com/css2?family=Marcellus&family=Open+Sans:wght@400;600;700&display=swap" rel="stylesheet">
<style>
  :root{
    --bg:#8fb9e3;
    --blue:#5b83ae;
    --blue-dark:#3f6a97;
    --blue-soft:#7c9dc2;
    --gold:#d8b66a;
    --paper:#ffffff;
    --ink-soft:#9aa7b5;
    --photo-deep:#3f5f86;
    --photo-mid:#6f8fb5;
    --photo-light:#b9c9dc;
    --mist:rgba(205,212,220,.45);
  }
  *{box-sizing:border-box;margin:0;padding:0}
  html,body{width:1200px;height:904px;overflow:hidden}
  body{background:var(--bg);position:relative;font-family:"Open Sans",Arial,sans-serif}
  .brand{font-family:"Marcellus",Georgia,serif;font-weight:400;color:var(--blue);white-space:nowrap}
  .piece{position:absolute;box-shadow:0 6px 18px rgba(30,60,100,.25)}

  /* Photo placeholders */
  .photo{position:absolute}
  .photo--vivid{background:linear-gradient(160deg,var(--photo-light) 0%,var(--photo-mid) 45%,var(--photo-deep) 100%);border-radius:4px}
  .photo--faint{background:radial-gradient(ellipse at center,var(--mist) 0%,rgba(225,230,236,.25) 45%,rgba(255,255,255,0) 70%)}

  /* Letterhead */
  .letterhead{left:60px;top:30px;width:340px;height:480px;background:var(--paper)}
  .letterhead__rule{position:absolute;top:45px;height:4px;width:80px}
  .letterhead__rule--gold{left:0;background:var(--gold)}
  .letterhead__rule--blue{right:0;background:var(--blue)}
  .letterhead__head{position:absolute;top:26px;left:0;right:0;display:flex;justify-content:center;align-items:center;gap:8px}
  .letterhead__thumb{position:relative;width:36px;height:36px;border-radius:4px}
  .letterhead__name{font-size:16px}
  .letterhead__mark{left:50px;top:150px;width:260px;height:300px}
  .letterhead__contact{position:absolute;left:10px;bottom:26px;font-size:6px;line-height:1.6;color:var(--blue-dark);font-weight:600}
  .letterhead__footer{position:absolute;left:0;right:0;bottom:0;height:14px;display:flex;align-items:flex-end}
  .letterhead__bar{height:3px;flex:1}
  .letterhead__url{background:var(--blue);color:#fff;font-size:6.5px;font-weight:700;height:14px;line-height:14px;padding:0 10px;width:100px;white-space:nowrap}

  /* Folder */
  .folder{left:440px;top:30px;width:720px;height:340px;display:flex;background:var(--blue)}
  .folder__panel{position:relative;width:50%;height:100%;overflow:hidden;
    background:linear-gradient(135deg,rgba(255,255,255,.08) 0 30%,transparent 30% 60%,rgba(255,255,255,.06) 60%)}
  .folder__panel + .folder__panel{border-left:1px solid rgba(255,255,255,.25)}
  .folder__band{position:absolute;left:0;right:0;top:80px;height:120px;background:var(--paper)}
  .folder__name{position:absolute;top:26px;left:0;right:0;text-align:center;color:#fff;font-size:20px}
  .folder__photo{left:130px;top:92px;width:100px;height:96px}
  .folder__contacts{position:absolute;top:218px;left:0;right:0;display:flex;justify-content:space-around;color:#fff;font-size:6.5px;font-weight:600;text-align:center}
  .folder__contacts svg{display:block;margin:0 auto 4px}
  .folder__services{position:absolute;left:0;right:0;bottom:0;height:62px;background:var(--paper);text-align:center;color:var(--blue-dark)}
  .folder__tab{display:inline-block;background:var(--blue-dark);color:#fff;font-size:6px;font-weight:700;padding:2px 14px;border-radius:0 0 6px 6px;letter-spacing:.5px}
  .folder__line{font-size:7px;font-weight:700;margin-top:7px;white-space:nowrap}
  .folder__seal{position:absolute;left:85px;top:50px;width:180px;height:180px;border-radius:50%;background:var(--paper);border:6px solid var(--blue-soft);display:flex;align-items:center;justify-content:center}
  .folder__seal .brand{font-size:18px}
  .folder__url{position:absolute;bottom:24px;left:0;right:0;text-align:center;color:#fff;font-size:11px;font-weight:700}

  /* Envelope */
  .envelope{left:60px;top:560px;width:480px;height:250px;background:var(--paper)}
  .envelope__name{position:absolute;left:22px;top:24px;font-size:22px}
  .envelope__address{position:absolute;left:22px;top:54px;font-size:6.5px;font-weight:700;color:var(--blue-dark)}
  .envelope__mark{left:230px;top:10px;width:220px;height:200px}
  .envelope__tagline{position:absolute;left:0;right:0;bottom:16px;text-align:center;font-size:15px;color:var(--ink-soft)}
  .envelope__rule{position:absolute;bottom:0;left:130px;width:200px;height:3px;background:var(--gold)}

  /* Business cards */
  .card{width:300px;height:170px;background:var(--blue);overflow:hidden;border-radius:8px}
  .card--front{left:590px;top:430px}
  .card--back{left:590px;top:640px}
  .card svg.swoosh{position:absolute;inset:0}
  .card--front .brand{position:absolute;right:26px;top:62px;color:#fff;font-size:20px}
  .card__person{position:absolute;left:16px;top:64px;color:#fff}
  .card__person b{display:block;font-size:10px}
  .card__person span{font-size:7px}
  .card__details{position:absolute;left:150px;top:44px;font-size:7px;line-height:2;color:var(--blue-dark)}
  .card__details .brand{font-size:14px;display:block;line-height:1.4;margin-bottom:4px}

  /* Notebook */
  .notebook{left:940px;top:420px;width:210px;height:300px;background:var(--blue);border-radius:4px 10px 10px 4px;overflow:hidden}
  .notebook__spine{position:absolute;left:0;top:0;bottom:0;width:6px;background:#6d7fc4}
  .notebook__name{position:absolute;top:26px;left:0;right:0;text-align:center;color:#fff;font-size:15px}
  .notebook__band{position:absolute;left:0;right:0;top:88px;height:90px;background:var(--paper)}
  .notebook__ring{position:absolute;left:55px;top:72px;width:120px;height:120px;border-radius:50%;border:5px solid var(--blue-soft);background:var(--paper);overflow:hidden}
  .notebook__ring .photo{inset:6px;border-radius:50%}
  .notebook__strap{position:absolute;top:0;bottom:0;right:24px;width:10px;background:#4a4f57}
  .notebook__tagline{position:absolute;bottom:38px;left:0;right:0;text-align:center;color:#fff;font-size:8.5px}
  .notebook__url{position:absolute;bottom:20px;left:0;right:0;text-align:center;color:#fff;font-size:7px;font-weight:700}
</style>
</head>
<body>

<section class="piece letterhead">
  <div class="letterhead__rule letterhead__rule--gold"></div>
  <div class="letterhead__rule letterhead__rule--blue"></div>
  <div class="letterhead__head">
    <div class="photo photo--vivid letterhead__thumb" role="img" aria-label="Small photograph of a leaping dancer in a flowing dress"></div>
    <div class="brand letterhead__name">Brennwald+Partner</div>
  </div>
  <div class="photo photo--faint letterhead__mark" role="img" aria-label="Faint photograph of a leaping dancer in a flowing dress"></div>
  <div class="letterhead__contact">
    <div>● Brennwald+Partner, Hallstein/Austria</div>
    <div>✉ info@brennwaldpartner.com</div>
  </div>
  <div class="letterhead__footer">
    <div class="letterhead__bar" style="background:var(--gold)"></div>
    <div class="letterhead__bar" style="background:var(--blue)"></div>
    <div class="letterhead__bar" style="background:var(--gold)"></div>
    <div class="letterhead__url">brennwaldpartner.com</div>
  </div>
</section>

<section class="piece folder">
  <div class="folder__panel">
    <div class="brand folder__name" style="color:#fff">Brennwald+Partner</div>
    <div class="folder__band"></div>
    <div class="photo photo--vivid folder__photo" role="img" aria-label="Photograph of a leaping dancer in a flowing blue dress"></div>
    <div class="folder__contacts">
      <div><svg width="12" height="12" viewBox="0 0 12 12"><circle cx="5" cy="5" r="3.5" fill="none" stroke="#fff" stroke-width="1.5"/><line x1="7.5" y1="7.5" x2="11" y2="11" stroke="#fff" stroke-width="1.5"/></svg>brennwaldpartner.com</div>
      <div><svg width="14" height="10" viewBox="0 0 14 10"><rect x="0.5" y="0.5" width="13" height="9" fill="#fff"/><polyline points="0.5,0.5 7,6 13.5,0.5" fill="none" stroke="#5b83ae"/></svg>info@brennwaldpartner.com</div>
      <div><svg width="12" height="11" viewBox="0 0 12 11"><polygon points="6,0 12,5 10,5 10,11 2,11 2,5 0,5" fill="#fff"/></svg>Hallstein/Austria</div>
    </div>
    <div class="folder__services">
      <span class="folder__tab">SERVICES</span>
      <div class="folder__line">Develop future potential | Interim management | Learning workshop for managers</div>
      <div class="folder__line" style="margin-top:3px">Succession scheme | Hotel concepts | Corporate culture development</div>
    </div>
  </div>
  <div class="folder__panel">
    <div class="folder__band"></div>
    <div class="folder__seal"><span class="brand">Brennwald+Partner</span></div>
    <div class="folder__url">brennwaldpartner.com</div>
  </div>
</section>

<section class="piece envelope">
  <div class="photo photo--faint envelope__mark" role="img" aria-label="Faint photograph of a leaping dancer in a flowing dress"></div>
  <div class="brand envelope__name">Brennwald+Partner</div>
  <div class="envelope__address">Brennwald+Partner, Hallstein/Austria</div>
  <div class="brand envelope__tagline">We are sparring partners for successful hotels</div>
  <div class="envelope__rule"></div>
</section>

<section class="piece card card--front">
  <svg class="swoosh" width="300" height="170" viewBox="0 0 300 170" aria-hidden="true">
    <path d="M0 0 H120 C60 50 60 120 110 170 H0 Z" fill="#c9ced6"/>
    <path d="M0 0 H95 C40 55 45 120 85 170 H0 Z" fill="#5b83ae"/>
  </svg>
  <div class="brand">Brennwald+Partner</div>
</section>

<section class="piece card card--back">
  <svg class="swoosh" width="300" height="170" viewBox="0 0 300 170" aria-hidden="true">
    <path d="M130 0 H300 V170 H140 C100 120 100 50 130 0 Z" fill="#fff"/>
    <path d="M130 0 C100 50 100 120 140 170 H128 C88 120 88 50 118 0 Z" fill="#c9ced6"/>
  </svg>
  <div class="card__person"><b>Sample Name</b><span>Consultant</span></div>
  <div class="card__details">
    <span class="brand">Brennwald+Partner</span>
    ● Hallstein/Austria<br>
    ✉ info@brennwaldpartner.com<br>
    ⌕ brennwaldpartner.com
  </div>
</section>

<section class="piece notebook">
  <div class="notebook__spine"></div>
  <div class="brand notebook__name" style="color:#fff">Brennwald+Partner</div>
  <div class="notebook__band"></div>
  <div class="notebook__ring">
    <div class="photo photo--vivid" role="img" aria-label="Photograph of a leaping dancer in a flowing blue dress"></div>
  </div>
  <div class="notebook__strap"></div>
  <div class="brand notebook__tagline" style="color:#fff">We are sparring partners for successful hotels</div>
  <div class="notebook__url">brennwaldpartner.com</div>
</section>

</body>
</html>
```